Kestrel Facilities Business Card Design

We would now like to design business cards with the new Kestrel Facilities logo

Target Market(s)

Professional

Industry/Entity Type

Professional services

Contact Information for Business Card

Employee name, title, phone number, email address, corporate office address and logo.

Font styles to use
Sans Serif

Colors
0054AA
0677BA
7BADD7
CADEEF
E8F1F8

Requirements
Must have
• My logo
Should not have
• any other pictures or images besides my logo

```html
<!DOCTYPE html>
<html lang="en">
<head>
<meta charset="utf-8">
<title>Kestrel Facilities – Business Card</title>
<link rel="stylesheet" href="https://fonts.googleapis.com/css2?family=Montserrat:wght@400;500;700&family=Josefin+Sans:wght@400&display=swap">
<style>
  :root {
    --brand-blue: #3578bf;
    --ink: #1c1c1c;
    --card: #ffffff;
    --backdrop: #8a8a8a;
  }
  * { margin: 0; padding: 0; box-sizing: border-box; }
  html, body {
    width: 1160px; height: 1200px; overflow: hidden;
    background: var(--backdrop);
  }
  .card {
    position: absolute; left: 199px; width: 778px; height: 442px;
    background: var(--card);
  }
  .card--front { top: 105px; }
  .card--back { top: 634px; }

  .accent-bar {
    position: absolute; left: 0; top: 76px; width: 17px; height: 53px;
    background: var(--brand-blue);
  }
  .person { position: absolute; left: 29px; top: 70px; font-family: "Montserrat", sans-serif; }
  .person__name {
    font-weight: 700; font-size: 31px; color: var(--brand-blue);
    letter-spacing: -0.5px; line-height: 36px;
  }
  .person__title { font-weight: 400; font-size: 21px; color: var(--ink); line-height: 28px; }

  .brand {
    position: absolute; display: flex; align-items: center; gap: 14px;
    font-family: "Montserrat", sans-serif; font-weight: 700; color: var(--brand-blue);
  }
  .brand__mark { background: var(--brand-blue); flex: none; }
  .brand__name { text-transform: uppercase; line-height: 1.05; letter-spacing: 1px; }
  .card--front .brand { right: 33px; top: 90px; }
  .card--front .brand__mark { width: 70px; height: 70px; }
  .card--front .brand__name { font-size: 30px; }
  .card--back .brand { left: 50%; top: 50%; transform: translate(-50%, -50%); gap: 20px; }
  .card--back .brand__mark { width: 110px; height: 110px; }
  .card--back .brand__name { font-size: 46px; }

  .contacts {
    position: absolute; left: 29px; top: 326px; list-style: none;
    font-family: "Montserrat", sans-serif; font-size: 20px; color: var(--ink);
  }
  .contacts li { display: flex; align-items: center; height: 29px; }
  .contacts svg { width: 19px; height: 17px; margin-right: 7px; fill: var(--brand-blue); }
  .contacts .contacts__phone { font-weight: 500; }

  .address {
    position: absolute; right: 33px; top: 354px; text-align: right;
    font-family: "Josefin Sans", sans-serif; font-size: 21px; color: var(--ink); line-height: 29px;
  }
</style>
</head>
<body>
  <section class="card card--front">
    <div class="accent-bar"></div>
    <div class="person">
      <div class="person__name">AMINA KARIUKI</div>
      <div class="person__title">Co-Founder</div>
    </div>

    <div class="brand">
      <span class="brand__mark"></span>
      <span class="brand__name">Kestrel<br>Facilities</span>
    </div>

    <ul class="contacts">
      <li class="contacts__phone">
        <svg viewBox="0 0 20 18" aria-hidden="true"><path d="M1 6c0-3 4-5 9-5s9 2 9 5v2h-5V6H6v2H1z"/><rect x="3" y="8" width="14" height="9" rx="1"/></svg>
        +254-100-55012
      </li>
      <li>
        <svg viewBox="0 0 20 18" aria-hidden="true"><path d="M1 3h18v12H1z M2 4l8 6 8-6" stroke="#fff" stroke-width="1.2"/></svg>
        info@kestrelfacilities.com
      </li>
      <li>
        <svg viewBox="0 0 20 18" aria-hidden="true"><circle cx="10" cy="9" r="8.5"/><path d="M5 6c2 0 3 2 5 1s1 4 3 4M12 3c0 2 2 2 4 3" stroke="#fff" stroke-width="1.2" fill="none"/></svg>
        www.kestrelfacilities.com
      </li>
    </ul>

    <address class="address" style="font-style:normal">
      P.O Box 4810-00200<br>Nairobi, Kenya
    </address>
  </section>

  <section class="card card--back">
    <div class="brand">
      <span class="brand__mark"></span>
      <span class="brand__name">Kestrel<br>Facilities</span>
    </div>
  </section>
</body>
</html>
```